New bussiness card, using company logo.
Lionel Brisk
Manager/Director
Brisk Property Developments
Po Box 5347
Thuringowa Central
Qld
0491 638 205
lionel@briskpropertydevelopments
eye catching, vibrant colours, professional

```html
<!DOCTYPE html>
<html lang="en">
<head>
<meta charset="utf-8">
<title>Brisk Property Developments – Business Cards</title>
<link rel="stylesheet" href="https://fonts.googleapis.com/css2?family=Questrial&display=swap">
<style>
  :root {
    --brand-green: #6cbb45;
    --brand-green-light: #8dc63f;
    --brand-red: #e0262e;
    --ink: #222222;
    --card-white: #ffffff;
    --stage: #6e3b2a;
  }
  * { margin: 0; padding: 0; box-sizing: border-box; }
  html, body {
    width: 1200px; height: 746px; overflow: hidden;
    background: var(--stage);
    font-family: "Questrial", "Century Gothic", sans-serif;
  }
  .canvas { position: relative; width: 1200px; height: 746px; }

  .card {
    position: absolute; width: 525px; height: 299px; overflow: hidden;
    box-shadow: 0 2px 6px rgba(0,0,0,.35);
  }
  .card--front { left: 47px; top: 35px; background: var(--card-white); }
  .card--white { left: 611px; top: 39px; width: 523px; background: var(--card-white); }
  .card--green { left: 48px; top: 394px; background: linear-gradient(135deg, var(--brand-green) 0%, var(--brand-green-light) 100%); }
  .card--red { left: 627px; top: 394px; background: var(--brand-red); }

  .wordmark {
    position: absolute; left: 0; right: 0;
    display: flex; align-items: center; justify-content: center; gap: 10px;
    font-weight: 400; letter-spacing: .5px; text-transform: uppercase;
    white-space: nowrap;
  }
  .wordmark__square { width: 16px; height: 16px; flex: none; }

  .card--front .wordmark { top: 80px; font-size: 25px; color: var(--brand-red); }
  .card--front .wordmark__square { background: var(--brand-green); }

  .card--white .wordmark { top: 138px; font-size: 28px; color: var(--brand-green); }
  .card--white .wordmark__square { background: var(--brand-green); }

  .card--green .wordmark, .card--red .wordmark { top: 160px; font-size: 26px; color: var(--card-white); }
  .card--green .wordmark__square, .card--red .wordmark__square { background: var(--card-white); }

  .address {
    position: absolute; top: 176px; left: 0; right: 0; text-align: center;
    font-size: 15px; color: var(--ink); letter-spacing: .4px; white-space: nowrap;
  }

  .contact-band {
    position: absolute; left: 0; bottom: 0; width: 100%; height: 97px;
    background: linear-gradient(90deg, var(--brand-green) 0%, var(--brand-green-light) 100%);
    color: var(--card-white); padding: 9px 0 0 27px;
  }
  .contact-band__name { font-size: 19px; letter-spacing: .5px; white-space: nowrap; }
  .contact-band__role { font-size: 15px; }
  .contact-band__line {
    display: flex; align-items: center; gap: 6px; margin-top: 8px; font-size: 16px; white-space: nowrap;
  }
  .contact-band__line--email { font-size: 13px; margin-top: 9px; }
  .contact-band__icon { width: 11px; height: 11px; fill: var(--card-white); flex: none; }

  .web {
    position: absolute; left: 0; right: 0; text-align: center;
    font-size: 14px; letter-spacing: 3px; white-space: nowrap;
  }
  .card--white .web { top: 251px; color: var(--ink); }
  .web__name { color: var(--brand-red); }
  .web__tail { color: var(--brand-green); }
  .card--green .web, .card--red .web { top: 254px; color: var(--card-white); }
</style>
</head>
<body>
<main class="canvas">

  <section class="card card--front">
    <div class="wordmark"><span class="wordmark__square"></span>Brisk Property Developments</div>
    <p class="address">Po Box 5347, Harbourvale Central , Wrn</p>
    <div class="contact-band">
      <p class="contact-band__name">Lionel Brisk, <span class="contact-band__role">Manager/Director</span></p>
      <p class="contact-band__line">
        <svg class="contact-band__icon" viewBox="0 0 24 24" aria-hidden="true"><path d="M6.6 10.8a15.1 15.1 0 0 0 6.6 6.6l2.2-2.2a1 1 0 0 1 1-.25 11.4 11.4 0 0 0 3.6.57 1 1 0 0 1 1 1V20a1 1 0 0 1-1 1A17 17 0 0 1 3 4a1 1 0 0 1 1-1h3.5a1 1 0 0 1 1 1 11.4 11.4 0 0 0 .57 3.6 1 1 0 0 1-.25 1z"/></svg>
        0491 638 205
      </p>
      <p class="contact-band__line contact-band__line--email">
        <svg class="contact-band__icon" viewBox="0 0 24 24" aria-hidden="true"><path d="M2 5h20v14H2z"/><path d="M2 5l10 8 10-8" fill="none" stroke="#6cbb45" stroke-width="2"/></svg>
        lionel@briskpropertydevelopments.com
      </p>
    </div>
  </section>

  <section class="card card--white">
    <div class="wordmark"><span class="wordmark__square"></span>Brisk Property</div>
    <p class="web">www.<span class="web__name">brisk</span><span class="web__tail">propertydevelopments</span>.com</p>
  </section>

  <section class="card card--green">
    <div class="wordmark"><span class="wordmark__square"></span>Brisk Property Developments</div>
    <p class="web">www.briskpropertydevelopments.com</p>
  </section>

  <section class="card card--red">
    <div class="wordmark"><span class="wordmark__square"></span>Brisk Property Developments</div>
    <p class="web">www.briskpropertydevelopments.com</p>
  </section>

</main>
</body>
</html>
```